Counseling Practice Business Card

I need a professional looking business card incorporating my new logo that was just completed. Card needs to incorporate my name and title, description of my specialty, my address, my phone number, my fax number, my email and my website URL. I need to be able to choose design on/with different paper colors and textures.
I do not have a lot of business card ideas so I am open to anything but I want bold,sharp, clear card without additional designs other than my logo (see attached file info). I am open to different color backgrounds or paper colors including black. I do not like traditional brackets around area codes in phone number or dashes between numbers in phone number. Am open to other ways of presenting including periods between numbers as appropriate. I do not know enough to know what I like yet but I want card to coordinate and work together with my logo. My practice emphasizes natural mental health interventions so any use of color (with background paper color or the blue and green in my logo) that elicits nature is nice. In addition to black, any natural brown or wood looking background might be desirable also. Most of the offerings so far look very similar and boring.

Target Market(s)

Potential therapy clients and other professionals

Contact Information for Business Card

Card information:
Gerald M. Whitcombe, Ph.D.
Licensed Clinical Psychologist
Integrative Health Coach
4812 Marlowe Ridge Blvd SE
Suite 310
Duluth, GA 30096
(770) 415-2983 phone
(770) 581-4096 fax
drgeraldwhitcombe@quillmarsh.net
brightfernwellness.net

Font styles to use
Serif
Sans Serif
Other font styles liked:
• anything that you think looks crisp, clear and easily readable

Requirements
Must have
• Any color used should coordinate with my logo design (see attached files).
• Card should be printed horizontally so top and bottom are longest sides of rectangle.
• Background color or paper color should complement and highlight logo. Do not like a white background. black, grey, brown or any color my logo would blend well with.
Nice to have
• I would like designer to utilize color to highlight letters/name or phone-fax-web symbols.
• Bottom edge of card could be highlighted if appropriate to an idea.
Should not have
• I would NOT want the card to have a pure white background at all.
• No clear cards.
• Cards should be oriented with long sides on bottom and top, NOT sides. DO NOT LIKE THIS THIN TALL ORIENTATION.

```html
<!DOCTYPE html>
<html lang="en">
<head>
<meta charset="utf-8">
<title>Brightfern Wellness – Business Card</title>
<link rel="stylesheet" href="https://fonts.googleapis.com/css2?family=Roboto:wght@400;500&family=Roboto+Condensed:wght@700&display=swap">
<style>
  :root {
    --stage: #3a3a3a;
    --card: #1d1d1f;
    --emboss: #3b3b3e;
    --brand-blue: #2a76c0;
    --brand-green: #17783a;
    --wave-dark: #2a2a2c;
    --ink-light: #f4f4f4;
  }
  * { margin: 0; padding: 0; box-sizing: border-box; }
  html, body {
    width: 799px; height: 1200px; overflow: hidden;
    background: var(--stage);
    font-family: "Roboto", Arial, sans-serif;
  }
  .sheet {
    position: relative; width: 799px; height: 1200px;
    display: flex; flex-direction: column; align-items: center;
    justify-content: space-around; padding: 60px 0;
  }
  .card {
    position: relative; width: 640px; height: 366px;
    background: var(--card); border-radius: 4px; overflow: hidden;
    box-shadow: 0 14px 30px rgba(0,0,0,.45);
  }
  /* front */
  .card--front { display: flex; align-items: center; justify-content: center; }
  .front-brand {
    font-weight: 500; font-size: 46px; letter-spacing: 1px;
    color: var(--emboss);
  }
  /* back */
  .back-brand {
    position: absolute; left: 40px; top: 44px;
    font-weight: 500; font-size: 32px; color: var(--brand-blue);
  }
  .holder { position: absolute; left: 40px; top: 112px; }
  .holder-name {
    font-family: "Roboto Condensed", "Arial Narrow", sans-serif;
    font-weight: 700; font-size: 24px; color: var(--brand-blue);
  }
  .holder-title { font-size: 14px; line-height: 1.3; color: var(--ink-light); margin-top: 4px; }
  .address {
    position: absolute; right: 40px; top: 120px; text-align: right;
    font-size: 15px; line-height: 1.35; color: var(--ink-light);
  }
  .waves { position: absolute; left: 0; top: 0; width: 640px; height: 366px; }
  .contact {
    position: absolute; right: 34px; top: 250px; list-style: none;
    color: var(--ink-light); font-size: 15px; line-height: 24px; text-align: right;
  }
  .contact li { display: flex; justify-content: flex-end; align-items: center; gap: 12px; }
  .contact svg { width: 15px; height: 15px; fill: var(--ink-light); flex: none; }
</style>
</head>
<body>
<main class="sheet">

  <section class="card card--front" aria-label="Card front">
    <div class="front-brand">Brightfern Wellness</div>
  </section>

  <section class="card card--back" aria-label="Card back">
    <svg class="waves" viewBox="0 0 640 366" preserveAspectRatio="none" aria-hidden="true">
      <path d="M0 196 C120 240 260 255 380 258 C500 260 580 236 640 226 L640 366 L0 366 Z" fill="var(--brand-green)"/>
      <path d="M0 210 C120 250 260 266 380 268 C500 270 580 246 640 236 L640 366 L0 366 Z" fill="var(--wave-dark)"/>
      <path d="M0 222 C140 252 280 272 390 276 C500 278 580 258 640 250 L640 366 L0 366 Z" fill="var(--brand-blue)"/>
    </svg>

    <div class="back-brand">Brightfern Wellness</div>

    <div class="holder">
      <div class="holder-name">Gerald M. Whitcombe, Ph.D.</div>
      <div class="holder-title">Licensed Clinical Psychologist/<br>Integrative Health Coach</div>
    </div>

    <address class="address" style="font-style:normal">
      4812 Marlowe Ridge Blvd SE<br>Suite 310 Duluth, GA 30096
    </address>

    <ul class="contact">
      <li>(770) 415-2983
        <svg viewBox="0 0 16 16"><path d="M3 1l3 3-2 2c1 2 3 4 5 5l2-2 3 3-2 3C6 14 2 10 1 3z"/></svg></li>
      <li>(770) 581-4096
        <svg viewBox="0 0 16 16"><path d="M4 1h8v4H4zM1 6h14v7h-3v2H4v-2H1zM5 11v3h6v-3z"/></svg></li>
      <li>www.brightfernwellness.net
        <svg viewBox="0 0 16 16"><path d="M8 1a7 7 0 100 14A7 7 0 008 1zm0 1.5c1 1 1.6 2.6 1.7 4.5H6.3C6.4 5.1 7 3.5 8 2.5zM2.6 7h2.2c.1-1.6.5-3 1.1-4A5.5 5.5 0 002.6 7zm8.6 0h2.2a5.5 5.5 0 00-3.3-4c.6 1 1 2.4 1.1 4zM2.6 9a5.5 5.5 0 003.3 4c-.6-1-1-2.4-1.1-4zm3.7 0c.1 1.9.7 3.5 1.7 4.5 1-1 1.6-2.6 1.7-4.5zm4.9 0c-.1 1.6-.5 3-1.1 4a5.5 5.5 0 003.3-4z"/></svg></li>
      <li>drgeraldwhitcombe@quillmarsh.net
        <svg viewBox="0 0 16 16"><path d="M1 3h14v10H1zm1.5 1.5L8 9l5.5-4.5v-.2h-11z"/></svg></li>
    </ul>
  </section>

</main>
</body>
</html>
```